Counseling Practice Business Card

I need a professional looking business card incorporating my new logo that was just completed. Card needs to incorporate my name and title, description of my specialty, my address, my phone number, my fax number, my email and my website URL. I need to be able to choose design on/with different paper colors and textures.
I do not have a lot of business card ideas so I am open to anything but I want bold,sharp, clear card without additional designs other than my logo (see attached file info). I am open to different color backgrounds or paper colors including black. I do not like traditional brackets around area codes in phone number or dashes between numbers in phone number. Am open to other ways of presenting including periods between numbers as appropriate. I do not know enough to know what I like yet but I want card to coordinate and work together with my logo. My practice emphasizes natural mental health interventions so any use of color (with background paper color or the blue and green in my logo) that elicits nature is nice. In addition to black, any natural brown or wood looking background might be desirable also. Most of the offerings so far look very similar and boring.

Target Market(s)

Potential therapy clients and other professionals

Contact Information for Business Card

Card information:
Gerald M. Whitcombe, Ph.D.
Licensed Clinical Psychologist
Integrative Health Coach
4812 Marlowe Ridge Blvd SE
Suite 310
Duluth, GA 30096
(770) 415-2983 phone
(770) 581-4096 fax
drgeraldwhitcombe@quillmarsh.net
brightfernwellness.net

Font styles to use
Serif
Sans Serif
Other font styles liked:
• anything that you think looks crisp, clear and easily readable

Requirements
Must have
• Any color used should coordinate with my logo design (see attached files).
• Card should be printed horizontally so top and bottom are longest sides of rectangle.
• Background color or paper color should complement and highlight logo. Do not like a white background. black, grey, brown or any color my logo would blend well with.
Nice to have
• I would like designer to utilize color to highlight letters/name or phone-fax-web symbols.
• Bottom edge of card could be highlighted if appropriate to an idea.
Should not have
• I would NOT want the card to have a pure white background at all.
• No clear cards.
• Cards should be oriented with long sides on bottom and top, NOT sides. DO NOT LIKE THIS THIN TALL ORIENTATION.

```html
<!DOCTYPE html>
<html lang="en">
<head>
<meta charset="utf-8">
<title>Brightfern Wellness – Business Card</title>
<link href="https://fonts.googleapis.com/css2?family=Lato:wght@400;700&display=swap" rel="stylesheet">
<style>
  :root{
    --stage:#1a1a1a;
    --card-light:#f3f3f3;
    --brand-blue:#1f6db5;
    --brand-green:#0b6b35;
    --gradient-top:#2471b5;
    --gradient-bottom:#006a2e;
    --ink:#333333;
    --ink-soft:#555555;
    --white:#ffffff;
  }
  html,body{margin:0;padding:0;overflow:hidden;}
  body{
    width:1200px;height:900px;background:var(--stage);
    position:relative;font-family:"Lato",sans-serif;
  }
  .card{
    position:absolute;top:295px;width:502px;height:310px;
    box-shadow:3px 4px 6px rgba(0,0,0,.55);
    box-sizing:border-box;
  }
  .card-front{
    left:78px;background:var(--card-light);
    border-radius:62px 0 62px 0;
  }
  .card-back{
    left:620px;
    background:linear-gradient(180deg,var(--gradient-top) 0%,var(--gradient-bottom) 100%);
    border-radius:0 62px 0 62px;
  }
  .brand-name{
    position:absolute;text-align:center;margin:0;
    font-weight:700;font-size:33px;line-height:36px;letter-spacing:.5px;
  }
  .card-front .brand-name{left:20px;width:190px;top:119px;color:var(--brand-blue);}
  .card-back .brand-name{left:0;right:0;top:110px;color:var(--white);}

  .front-divider{
    position:absolute;left:218px;top:50px;width:2px;height:210px;
    background:var(--brand-green);opacity:.35;
  }

  .details{position:absolute;left:238px;top:46px;}
  .practitioner{margin:0 0 10px;}
  .name{
    margin:0;font-size:15.5px;font-weight:700;text-transform:uppercase;
    letter-spacing:.3px;color:var(--brand-blue);line-height:20px;white-space:nowrap;
  }
  .name .surname{color:var(--brand-green);}
  .role{margin:0;font-size:13.5px;color:var(--ink);line-height:18px;}

  .address{
    margin:0 0 10px 2px;font-style:normal;
    font-size:13px;line-height:18px;color:var(--ink-soft);
  }
  .contacts{
    margin:0;padding:0;list-style:none;
    font-size:13.5px;line-height:18px;color:var(--ink);
  }
  .contacts li{display:flex;align-items:center;white-space:nowrap;}
  .contacts svg{width:12px;height:12px;margin-right:5px;fill:var(--brand-blue);flex:none;}

  .web-url{
    position:absolute;left:0;right:0;top:246px;text-align:center;margin:0;
    color:var(--white);font-size:14px;font-weight:700;letter-spacing:.3px;
  }
</style>
</head>
<body>

<section class="card card-front" aria-label="Card front">
  <p class="brand-name">Brightfern<br>Wellness</p>
  <div class="front-divider"></div>

  <div class="details">
    <div class="practitioner">
      <p class="name">Gerald M. <span class="surname">Whitcombe</span>, Ph.D.</p>
      <p class="role">Licensed Clinical Psychologist</p>
      <p class="role">Integrative Health Coach</p>
    </div>

    <address class="address">
      4812 Marlowe Ridge Blvd SE<br>
      Suite 310 Duluth, GA 30096
    </address>

    <ul class="contacts">
      <li>
        <svg viewBox="0 0 12 12" aria-hidden="true"><path d="M1 4.5C1 2.5 3.5 1.5 6 1.5S11 2.5 11 4.5L9 5 8.5 3.8H3.5L3 5z"/><rect x="2.5" y="5.5" width="7" height="5" rx="1"/></svg>
        770.415.2983
      </li>
      <li>
        <svg viewBox="0 0 12 12" aria-hidden="true"><rect x="3" y="1" width="6" height="3"/><rect x="1" y="4.5" width="10" height="4.5" rx="1"/><rect x="3" y="8" width="6" height="3"/></svg>
        770.581.4096
      </li>
      <li>
        <svg viewBox="0 0 12 12" aria-hidden="true"><path d="M1 2.5h10v7H1z M1.5 3l4.5 3.5L10.5 3" stroke="#f3f3f3" stroke-width="1"/></svg>
        drgeraldwhitcombe@quillmarsh.net
      </li>
      <li>
        <svg viewBox="0 0 12 12" aria-hidden="true"><circle cx="6" cy="6" r="5.5"/><path d="M3.5 3.5c1 .5 1 1.5 2 1.5s1 1.5 0 2 0 2-1 2M8 2.5c-.5 1 .5 1.5 1.5 1.5M9 7.5c-1 0-1.5 1-1 2" stroke="#f3f3f3" stroke-width=".8" fill="none"/></svg>
        brightfernwellness.net
      </li>
    </ul>
  </div>
</section>

<section class="card card-back" aria-label="Card back">
  <p class="brand-name">Brightfern<br>Wellness</p>
  <p class="web-url">brightfernwellness.net</p>
</section>

</body>
</html>
```